Orthobiologic, StemCell, Bone Marrow Aspirate Device Distributor

We need a wordpress fully functioning website design for an innovative ortho-biologic, Bone Marrow Aspirate Device that extracts stem cells for orthopedic regenerative medical professionals. We also offer state of the art training in there office setting with licensed medical staff, a full service support team, and software for tracking patient outcome over time. We are an innovative company that prides itself on gold standard support. We will have other offerings on our website and would like a spot for "future" products. We would like to see designs that look professional, medical, and convey support, security, science, and innovation. We prefer shades of blue and red/orange. I particularly like the following websites that also sell the same device in order of preference:regenacelltherapy.comhttps://aspire-medical.eu/marrow-cellution/https://www.matrixbiosurgical.com/#emerging-solutions-in-healthcareElite2elite.comI have attached a few pictures of the device for reference

Target Market(s)

Orthopedics, Regenerative medicine doctors, Industry representatives, Hospitals

Industry/Entity Type

Medical Equipment

Coding

Coded - Design and coding required

Colors
3176b5
33a6d7
f37022
ec1f27

Requirements
Must have
• It must be able to have videos which I can supply, email, online ordering, and sfax. I have a domain name Coralweavesolutions.com . It must have a FAQ section which you can obtain some information from https://www.tolvenclinical.com/solutions#resources
• The device is manufactured by Dulmor and this is the link to the product page http://www.dulmor.com/quintadraw
• I am currently working on a custom logo and should be able to supply that in short order. I prefer shades of blue and red.
Nice to have
• I would love to have a graphic video as seen here: please see quinta draw vs bone marrow aspirate concentrate.
• https://www.tolvenclinical.com/solutions#competition
• I would pay considerably more to have something similar if it is at all possible
Should not have
• Nothing specific

```html
<!DOCTYPE html>
<html lang="en">
<head>
<meta charset="utf-8">
<title>Coralweave Solutions</title>
<link href="https://fonts.googleapis.com/css2?family=Lato:wght@300;400;700;900&display=swap" rel="stylesheet">
<style>
:root{
  --blue:#3176b5;
  --blue-deep:#143f93;
  --sky:#33a6d7;
  --orange:#f37022;
  --red:#ec1f27;
  --ink:#2b2b2b;
  --text:#5a5a5a;
  --pale:#d9e7f0;
  --foot:#f1f1f1;
  --white:#ffffff;
}
*{margin:0;padding:0;box-sizing:border-box}
html,body{width:1200px;height:4505px;overflow:hidden}
body{font-family:'Lato',sans-serif;color:var(--text);background:var(--white);position:relative}
section,header,footer{position:absolute;left:0;width:1200px}
.abs{position:absolute}
.center{text-align:center}

/* header */
.site-header{top:0;height:95px;background:var(--white)}
.brand{left:148px;top:20px;color:var(--blue)}
.brand-name{font-size:26px;font-weight:900;letter-spacing:0.5px;line-height:28px}
.brand-sub{font-size:21px;font-weight:400;letter-spacing:5.2px;line-height:24px}
.nav{top:38px;left:0;font-size:17px;color:var(--ink);font-weight:400}
.nav span{position:absolute;white-space:nowrap}

/* hero */
.hero{top:95px;height:569px;background:radial-gradient(ellipse at 55% 35%,#3f7fd6 0%,#1d56b8 40%,#0f3a92 100%)}
.hero-title{top:210px;width:1200px;font-size:46px;color:var(--white);font-weight:700}
.hero-sub{top:280px;width:1200px;font-size:24px;color:var(--white);font-weight:300}
.hero-arrow{top:229px;width:56px;height:56px;border-radius:50%;background:rgba(40,60,100,.55)}

/* about */
.about{top:664px;height:379px}
.section-title{font-weight:400;color:var(--blue)}
.about h2{top:84px;width:1200px;font-size:33px}
.about p{top:148px;left:250px;width:700px;font-size:17px;line-height:27px}
.about svg{left:580px;top:268px}

/* advantage */
.advantage{top:1043px;height:455px;background:var(--pale)}
.advantage .photo{left:60px;top:0;width:540px;height:455px;background:radial-gradient(ellipse at 50% 55%,#6a9fd6 0%,#a9c6e6 45%,#d9e7f0 80%)}
.advantage h2{left:607px;top:84px;font-size:30px;color:var(--ink);font-weight:400}
.small-copy{font-size:13.5px;line-height:21px;color:var(--text)}
.advantage .p1{left:612px;top:142px;width:440px}
.advantage .p2{left:612px;top:227px;width:440px}
.btn{display:flex;align-items:center;justify-content:center;border-radius:30px;font-size:15px;font-weight:700}
.btn-blue{left:613px;top:328px;width:164px;height:49px;border:2px solid var(--blue);color:var(--blue)}

/* mission */
.mission{top:1498px;height:542px}
.mission h2{font-size:28px;top:86px}
.mission .m-title{left:167px}
.mission .w-title{left:607px}
.mission .mp{left:172px;width:395px}
.item-icon{left:612px}
.item-title{left:698px;font-size:18px;font-weight:700;color:var(--ink)}
.item-copy{left:699px;width:370px}

/* why band */
.why{top:2040px;height:524px;background:radial-gradient(ellipse at 50% 50%,#6d6d6d 0%,#3a3a3a 55%,#141414 100%)}
.why-box{left:264px;top:76px;width:667px;height:364px;background:rgba(38,110,190,.9)}
.why-box h2{top:68px;width:667px;font-size:32px;color:var(--white);font-weight:400}
.why-box p{top:124px;left:60px;width:547px;font-size:17px;line-height:27px;color:var(--white)}
.btn-white{left:252px;top:254px;width:162px;height:46px;border:2px solid var(--white);color:var(--white)}

/* products */
.products{top:2564px;height:591px}
.products h2{top:72px;width:1200px;font-size:30px;color:var(--ink);font-weight:400}
.card{top:148px;width:278px;height:362px;border:2px solid #e4e4e4;background:var(--white)}
.card .shot{left:40px;top:20px;width:194px;height:150px;background:linear-gradient(135deg,#f1f1f1,#d5d8de)}
.card h3{top:210px;width:274px;font-size:18px;font-weight:700;color:var(--ink)}
.card p{top:238px;left:25px;width:224px;font-size:13px;line-height:21px}
.btn-red{left:68px;top:288px;width:140px;height:41px;border:2px solid var(--red);color:var(--red);font-size:12px;font-weight:400}

/* faq */
.faq{top:3155px;height:580px;background:linear-gradient(100deg,var(--orange) 0%,#ef4a24 45%,var(--red) 100%)}
.faq h2{top:50px;width:1200px;font-size:33px;color:var(--white);font-weight:400}
.faq-item{left:222px;width:763px;border:2px solid rgba(255,255,255,.85);color:var(--white)}
.faq-q{position:absolute;left:24px;font-size:14px;font-weight:700;line-height:21px;width:640px;text-transform:uppercase}
.faq-a{position:absolute;left:24px;font-size:13.5px;line-height:19px;width:700px}
.faq-toggle{position:absolute;right:22px;font-size:26px;font-weight:400;line-height:26px}

/* tiles */
.tiles{top:3735px;height:375px}
.tile{top:0;height:375px}
.tile-a{left:0;width:397px;background:radial-gradient(ellipse at 50% 55%,#2c4a7a 0%,#13213f 75%)}
.tile-b{left:397px;width:405px;background:linear-gradient(135deg,#2f6fcf,#1849a8)}
.tile-c{left:802px;width:398px;background:radial-gradient(ellipse at 50% 55%,#2c4a8a 0%,#101c3a 75%)}
.tile h2{top:137px;width:100%;font-size:28px;color:var(--white);font-weight:400}
.tile .btn{top:190px;width:140px;height:41px;border:2px solid var(--white);color:var(--white);font-size:12px;font-weight:400}

/* footer */
.site-footer{top:4110px;height:395px;background:var(--foot)}
.f-head{top:80px;font-size:15px;font-weight:900;color:var(--ink)}
.f-list{top:112px;font-size:13.5px;line-height:26.5px;color:#555}
.f-contact{left:170px;top:112px;font-size:13.5px;color:#555}
.f-row{position:absolute;left:0;display:flex;gap:10px;white-space:nowrap;line-height:17px}
.social{display:flex;align-items:center;gap:10px;height:34px}
.dot{width:22px;height:22px;border-radius:50%;background:var(--blue)}
.rule{top:325px;left:0;width:1200px;height:1px;background:#d8d8d8}
.copy{top:350px;width:1200px;font-size:13.5px;color:#9a9a9a}
</style>
</head>
<body>

<header class="site-header">
  <div class="abs brand">
    <div class="brand-name">CORALWEAVE</div>
    <div class="brand-sub">SOLUTIONS</div>
  </div>
  <nav class="abs nav">
    <span style="left:411px">ABOUT</span>
    <span style="left:511px">PRODUCTS</span>
    <span style="left:645px">SERVICES</span>
    <span style="left:766px">SOLUTION</span>
    <span style="left:892px">NEWS</span>
    <span style="left:983px">CONTACT</span>
  </nav>
</header>

<section class="hero" role="img" aria-label="Blue x-ray of a human skeleton torso and shoulder">
  <div class="abs hero-arrow" style="left:106px">
    <svg width="56" height="56"><path d="M32 18 L22 28 L32 38" fill="none" stroke="#fff" stroke-width="3"/></svg>
  </div>
  <div class="abs hero-arrow" style="left:1066px">
    <svg width="56" height="56"><path d="M24 18 L34 28 L24 38" fill="none" stroke="#fff" stroke-width="3"/></svg>
  </div>
  <h1 class="abs center hero-title">INNOVATIVE ORTHO-BIOLOGIC</h1>
  <p class="abs center hero-sub">EXTRACTS STEM CELLS FOR ORTHOPEDIC REGENERATIVE</p>
</section>

<section class="about">
  <h2 class="abs center section-title">ABOUT CORALWEAVE SOLUTIONS</h2>
  <p class="abs center">Duis non nunc Nulla rhoncus dictum metus Curabitur tristique mi condimentum orci Phasellus pellentesque aliquam enim Proin dui lectus cursus eu mattis laoreet viverra sit amet quam Curabitur vel dolor ultrices ipsum dictum tristique</p>
  <svg class="abs" width="40" height="50" viewBox="0 0 40 50"><path d="M20 2 V46 M6 32 L20 46 L34 32" fill="none" stroke="#3176b5" stroke-width="2.5"/></svg>
</section>

<section class="advantage">
  <div class="abs photo" role="img" aria-label="Blue x-ray of the pelvis and lower spine"></div>
  <h2 class="abs">OUR ADVANTAGE</h2>
  <p class="abs small-copy p1">Sed porta Suspendisse quam leo molestie sed luctus quis feugiat in pede Fusce tellus Sed metus augue convallis et vehicula ut pulvinar eu ante Integer orci tellus</p>
  <p class="abs small-copy p2">Curabitur tristique mi condimentum orci Phasellus pellentesque aliquam enim Proin dui lectus cursus eu mattis laoreet viverra sit amet quam Curabitur</p>
  <div class="abs btn btn-blue">CLICK HERE</div>
</section>

<section class="mission">
  <h2 class="abs section-title m-title">OUR MISSION</h2>
  <h2 class="abs section-title w-title">WHY WE ARE</h2>
  <p class="abs small-copy mp" style="top:150px">Sed porta Suspendisse quam leo molestie sed luctus quis feugiat in pede Fusce tellus Sed metus augue convallis et vehicula ut pulvinar eu ante Integer orci tellus tristique vitae consequat nec porta vel lectus Nulla sit amet diam Duis non nunc Nulla rhoncus dictum metus</p>
  <p class="abs small-copy mp" style="top:280px">Curabitur tristique mi condimentum orci Phasellus pellentesque aliquam enim Proin dui lectus cursus eu mattis laoreet viverra sit amet quam Curabitur vel dolor ultrices ipsum dictum tristique Praesent vitae lacus</p>
  <p class="abs small-copy mp" style="top:388px">Ut velit enim vestibulum non fermentum nec hendrerit quis leo Pellentesque rutrum malesuada neque</p>

  <svg class="abs item-icon" style="top:145px" width="66" height="70" viewBox="0 0 66 70" fill="none" stroke="#f37022" stroke-width="2">
    <path d="M33 6 C19 6 11 16 11 27 C11 36 18 41 21 47 H45 C48 41 55 36 55 27 C55 16 47 6 33 6 Z"/>
    <path d="M23 53 H43 M25 59 H41 M29 65 H37 M33 16 V40 M24 26 H42"/>
  </svg>
  <div class="abs item-title" style="top:166px">INNOVATIVE</div>
  <p class="abs small-copy item-copy" style="top:195px">Vivamus porttitor purus nisi eleifend libero a tempus libero lectus feugiat felis Morbi diam mauris viverra in</p>

  <svg class="abs item-icon" style="top:265px" width="66" height="66" viewBox="0 0 66 66" fill="none" stroke="#f37022" stroke-width="2">
    <circle cx="33" cy="33" r="28"/><circle cx="33" cy="33" r="20"/>
    <path d="M33 33 L44 24 M20 40 H46 M33 17 V21"/>
  </svg>
  <div class="abs item-title" style="top:286px">EFFICIENT</div>
  <p class="abs small-copy item-copy" style="top:315px">Vivamus porttitor purus nisi eleifend libero a tempus libero lectus feugiat felis Morbi diam mauris</p>

  <svg class="abs item-icon" style="top:380px" width="66" height="70" viewBox="0 0 66 70" fill="none" stroke="#f37022" stroke-width="2">
    <circle cx="36" cy="30" r="24"/><circle cx="36" cy="30" r="9"/>
    <path d="M14 40 L6 62 L24 52"/>
  </svg>
  <div class="abs item-title" style="top:402px">SPECIFIC</div>
  <p class="abs small-copy item-copy" style="top:431px">Vivamus porttitor purus nisi eleifend libero a tempus libero lectus feugiat felis Morbi diam mauris</p>
</section>

<section class="why" role="img" aria-label="Grey x-ray of the hip joint">
  <div class="abs why-box">
    <h2 class="abs center">WHY WE ARE</h2>
    <p class="abs center">Duis non nunc Nulla rhoncus dictum metus Curabitur tristique mi condimentum orci Phasellus pellentesque aliquam enim Proin dui lectus cursus eu mattis laoreet viverra sit amet quam Curabitur vel dolor ultrices ipsum dictum tristique a</p>
    <div class="abs btn btn-white">CLICK HERE</div>
  </div>
</section>

<section class="products">
  <h2 class="abs center">OUR PRODUCTS</h2>
  <div class="abs card" style="left:160px">
    <div class="abs shot" role="img" aria-label="Aspiration needle with green handle"></div>
    <h3 class="abs center">PRODUCT TITLE</h3>
    <p class="abs center">Sed ut perspiciatis unde omnis iste natus error sit voluptatem</p>
    <div class="abs btn btn-red">CLICK HERE</div>
  </div>
  <div class="abs card" style="left:457px">
    <div class="abs shot" role="img" aria-label="Blue aspiration device with threaded shaft"></div>
    <h3 class="abs center">PRODUCT TITLE</h3>
    <p class="abs center">Sed ut perspiciatis unde omnis iste natus error sit voluptatem</p>
    <div class="abs btn btn-red">CLICK HERE</div>
  </div>
  <div class="abs card" style="left:752px">
    <div class="abs shot" role="img" aria-label="Steel cannula tip close-up"></div>
    <h3 class="abs center">PRODUCT TITLE</h3>
    <p class="abs center">Sed ut perspiciatis unde omnis iste natus error sit voluptatem</p>
    <div class="abs btn btn-red">CLICK HERE</div>
  </div>
</section>

<section class="faq">
  <h2 class="abs center">FAQ</h2>
  <div class="abs faq-item" style="top:112px;height:133px">
    <div class="faq-q" style="top:14px">Does a small volume aspirate have more CFU-F than a larger draw that is then volume reduced by centrifugation?</div>
    <div class="faq-a" style="top:68px">Pellentesque faucibus Ut accumsan ultricies elit Maecenas at justo id velit placerat molestie Donec dictum lectus non odio Cras a ante vitae enim iaculis aliquam Mauris nunc quam venenatis nec</div>
    <div class="faq-toggle" style="top:14px">–</div>
  </div>
  <div class="abs faq-item" style="top:258px;height:72px">
    <div class="faq-q" style="top:14px">What are the limitations of traditional needles and what is the optimal technique for minimizaing peripheral blood dilution?</div>
    <div class="faq-toggle" style="top:20px">+</div>
  </div>
  <div class="abs faq-item" style="top:345px;height:72px">
    <div class="faq-q" style="top:14px">Do I need to filter spicules from marrow after aspiration and are red cells a problem?</div>
    <div class="faq-toggle" style="top:20px">+</div>
  </div>
  <div class="abs faq-item" style="top:428px;height:74px">
    <div class="faq-q" style="top:14px">Is there a relationship between differing volumes of bone marrow aspirates and their cellular composition?</div>
    <div class="faq-toggle" style="top:20px">+</div>
  </div>
</section>

<section class="tiles">
  <div class="abs tile tile-a" role="img" aria-label="Dark blue x-ray of the ribcage">
    <h2 class="abs center">DISTRIBUTORS</h2>
    <div class="abs btn" style="left:124px">CLICK HERE</div>
  </div>
  <div class="abs tile tile-b" role="img" aria-label="Blue toned x-ray film being examined">
    <h2 class="abs center">OUR BLOGS</h2>
    <div class="abs btn" style="left:137px">CLICK HERE</div>
  </div>
  <div class="abs tile tile-c" role="img" aria-label="Dark blue x-ray of the pelvis">
    <h2 class="abs center">RESOURCES</h2>
    <div class="abs btn" style="left:134px">CLICK HERE</div>
  </div>
</section>

<footer class="site-footer">
  <div class="abs f-head" style="left:170px">CONTACT US</div>
  <div class="abs f-contact">
    <div class="f-row" style="top:0">
      <svg width="16" height="18" viewBox="0 0 16 18"><path d="M8 1 C4 1 2 4 2 7 C2 11 8 17 8 17 C8 17 14 11 14 7 C14 4 12 1 8 1 Z" fill="none" stroke="#333" stroke-width="1.5"/><circle cx="8" cy="7" r="2" fill="#333"/></svg>
      <span>48 Larkmoor Avenue #B<br>Austin 73301 TX</span>
    </div>
    <div class="f-row" style="top:50px">
      <svg width="16" height="16" viewBox="0 0 16 16"><path d="M3 1 L6 1 L7 5 L5 6 C6 8 8 10 10 11 L11 9 L15 10 L15 13 C15 14 14 15 13 15 C7 15 1 9 1 3 C1 2 2 1 3 1 Z" fill="none" stroke="#333" stroke-width="1.3"/></svg>
      <span>512.555.0148</span>
    </div>
    <div class="f-row" style="top:86px">
      <svg width="16" height="14" viewBox="0 0 16 14"><rect x="1" y="2" width="14" height="10" fill="none" stroke="#333" stroke-width="1.3"/><path d="M1 2 L8 8 L15 2" fill="none" stroke="#333" stroke-width="1.3"/></svg>
      <span>info@coralweavesolutions.com</span>
    </div>
  </div>

  <div class="abs f-head" style="left:425px">COMPANY</div>
  <div class="abs f-list" style="left:429px">Home<br>About us<br>Services<br>Products<br>Contact</div>

  <div class="abs f-head" style="left:571px">PRODUCTS</div>
  <div class="abs f-list" style="left:574px">Sed porta<br>Suspendisse quam<br>Leo molestie<br>Sed luctus<br>Fermentum</div>

  <div class="abs f-head" style="left:750px">RESOURCES</div>
  <div class="abs f-list" style="left:753px">FAQ<br>Videos<br>News<br>Contact Us</div>

  <div class="abs f-head" style="left:914px">GET IN TOUCH</div>
  <div class="abs f-list" style="left:917px;top:108px;line-height:normal">
    <div class="social"><span class="dot"></span>Chirpline</div>
    <div class="social"><span class="dot"></span>Facecircle</div>
    <div class="social"><span class="dot"></span>Workweb</div>
    <div class="social"><span class="dot"></span>Pictogrid</div>
  </div>

  <div class="abs rule"></div>
  <div class="abs center copy">Copyright © 2019 All right reserved</div>
</footer>

</body>
</html>
```